Lumavento business card

We need a modern business card - With our 4 colors - See web: www.lumavento.dk

I have attached logo and som old business Cards we have - Lets Make the new ones shine...:-) -

Industry/Entity Type

Business

Requirements
Must have
• the logo with lumavento only,

```html
<!DOCTYPE html>
<html lang="da">
<head>
<meta charset="utf-8">
<title>Lumavento business card</title>
<link rel="stylesheet" href="https://fonts.googleapis.com/css2?family=Open+Sans:wght@400;600;700&display=swap">
<style>
  :root {
    --page: #e4e2df;
    --card-top: #f4f3f1;
    --card-bottom: #e9e6e3;
    --brand-green: #5a9e2f;
    --brand-purple: #5b2a6e;
    --brand-magenta: #8e1c4f;
    --brand-orange: #cf5a14;
    --accent-orange: #e07a1c;
    --ink-soft: #6b6b6b;
    --ink-light: #fbeee6;
  }
  html, body {
    margin: 0;
    padding: 0;
    width: 1200px;
    height: 969px;
    overflow: hidden;
    background: var(--page);
    font-family: "Open Sans", Arial, sans-serif;
  }
  .card {
    position: absolute;
    left: 100px;
    top: 197px;
    width: 1000px;
    height: 575px;
    border-radius: 30px;
    overflow: hidden;
    background: linear-gradient(160deg, var(--card-top), var(--card-bottom));
    box-shadow: 0 10px 30px rgba(0,0,0,0.12);
  }
  .card__art {
    position: absolute;
    inset: 0;
  }
  .holder {
    position: absolute;
    left: 46px;
    top: 40px;
  }
  .holder__name {
    margin: 0;
    font-size: 33px;
    font-weight: 700;
    color: var(--brand-green);
    line-height: 1.1;
  }
  .holder__title {
    margin: 6px 0 0;
    font-size: 25px;
    font-weight: 600;
    color: var(--accent-orange);
  }
  .brand {
    position: absolute;
    left: 186px;
    top: 220px;
    width: 382px;
    text-align: center;
  }
  .brand__mark {
    display: inline-block;
    width: 22px;
    height: 22px;
    border-radius: 50%;
    background: var(--accent-orange);
    vertical-align: middle;
    margin-right: 10px;
  }
  .brand__name {
    font-size: 44px;
    font-weight: 400;
    letter-spacing: 2px;
    color: var(--brand-orange);
    vertical-align: middle;
  }
  .brand__rule {
    height: 4px;
    background: var(--brand-green);
    margin-top: 20px;
  }
  .brand__tagline {
    margin: 18px 0 0;
    font-size: 23px;
    color: var(--brand-orange);
  }
  .contact {
    position: absolute;
    right: 45px;
    top: 330px;
    margin: 0;
    padding: 0;
    list-style: none;
    text-align: right;
    font-size: 24px;
    color: var(--ink-light);
  }
  .contact li {
    height: 41px;
    line-height: 41px;
  }
  .contact svg {
    width: 22px;
    height: 22px;
    margin-left: 12px;
    vertical-align: -3px;
    fill: var(--ink-light);
  }
  .contact .contact__address {
    padding-right: 0;
  }
</style>
</head>
<body>
  <div class="card">
    <svg class="card__art" viewBox="0 0 1000 575" preserveAspectRatio="none" aria-hidden="true">
      <defs>
        <clipPath id="below-swoosh">
          <path d="M0,482 C300,470 650,420 800,260 S980,60 1000,12 L1000,575 L0,575 Z"/>
        </clipPath>
        <linearGradient id="fade-up" x1="0" y1="0" x2="0" y2="1">
          <stop offset="0" stop-color="#fff" stop-opacity="0.55"/>
          <stop offset="0.75" stop-color="#fff" stop-opacity="0"/>
        </linearGradient>
      </defs>
      <g clip-path="url(#below-swoosh)">
        <rect class="band band--green" x="0" y="0" width="227" height="575" fill="var(--brand-green)"/>
        <rect class="band band--purple" x="227" y="0" width="255" height="575" fill="var(--brand-purple)"/>
        <rect class="band band--magenta" x="482" y="0" width="361" height="575" fill="var(--brand-magenta)"/>
        <rect class="band band--orange" x="843" y="0" width="157" height="575" fill="var(--brand-orange)"/>
        <rect x="0" y="0" width="1000" height="470" fill="url(#fade-up)"/>
      </g>
      <path class="swoosh swoosh--main" d="M0,482 C300,470 650,420 800,260 S980,60 1000,12" fill="none" stroke="var(--accent-orange)" stroke-width="9"/>
      <path class="swoosh swoosh--light" d="M0,470 C300,458 640,408 790,250 S970,50 995,4" fill="none" stroke="#ffffff" stroke-opacity="0.8" stroke-width="3"/>
    </svg>

    <div class="holder">
      <p class="holder__name">Anja Holmvik</p>
      <p class="holder__title">Salgsdirektør</p>
    </div>

    <div class="brand">
      <span class="brand__mark"></span><span class="brand__name">lumavento</span>
      <div class="brand__rule"></div>
      <p class="brand__tagline">medier til unge</p>
    </div>

    <ul class="contact">
      <li>+45 31 40 72 16<svg viewBox="0 0 24 24"><path d="M6.6 10.8a15.1 15.1 0 0 0 6.6 6.6l2.2-2.2a1 1 0 0 1 1-.25 11.4 11.4 0 0 0 3.6.57 1 1 0 0 1 1 1V20a1 1 0 0 1-1 1A17 17 0 0 1 3 4a1 1 0 0 1 1-1h3.5a1 1 0 0 1 1 1c0 1.25.2 2.45.57 3.57a1 1 0 0 1-.25 1z"/></svg></li>
      <li>+45 52 18 63 04<svg viewBox="0 0 24 24"><path d="M6.6 10.8a15.1 15.1 0 0 0 6.6 6.6l2.2-2.2a1 1 0 0 1 1-.25 11.4 11.4 0 0 0 3.6.57 1 1 0 0 1 1 1V20a1 1 0 0 1-1 1A17 17 0 0 1 3 4a1 1 0 0 1 1-1h3.5a1 1 0 0 1 1 1c0 1.25.2 2.45.57 3.57a1 1 0 0 1-.25 1z"/></svg></li>
      <li>ah@lumavento.dk<svg viewBox="0 0 24 24"><path d="M2 5h20v14H2z M3 6l9 7 9-7" fill="none" stroke="var(--ink-light)" stroke-width="2"/><path d="M2 5h20v2l-10 7L2 7z"/></svg></li>
      <li>www.lumavento.dk<svg viewBox="0 0 24 24"><circle cx="12" cy="12" r="9" fill="none" stroke="var(--ink-light)" stroke-width="2"/><path d="M3 12h18M12 3c3 3 3 15 0 18M12 3c-3 3-3 15 0 18" fill="none" stroke="var(--ink-light)" stroke-width="1.6"/></svg></li>
      <li class="contact__address">Kastanjevej 8, 2000 Frederiksberg</li>
    </ul>
  </div>
</body>
</html>
```